Summit Builders Web Site / Business Cards

Construction Company that specializes in Water and Fire Damage, Residential ReModels, Landscaping and Building ADU (Accessory Dwelling Unit)

Growing and changing families often need additional space, and a remodeling project can often provide that. Adding a new area, or repurposing an existing one can satisfy this requirement.

Other times, homeowners want to update the look in their kitchen or bathroom with more than just a change of cabinetry or vanity doors and drawers. Whatever your needs are, Summit Builders has skilled workers who are bonded and insured, and ready to make your dreams and visions a reality.

Target Market(s)

Home Owners

Industry/Entity Type

Construction Company

Contact Information for Business Card

Center Logo with our information on the corners

Back side to be Logo Only
Contact Info
CSLB License # 2418596
info@summitbuildersca.example
www.summitbuildersca.example

Coding

Coded - Design and coding required

Number of Pages Required

5+ page

Font styles to use
Serif
Sans Serif

Requirements
Must have
• Using our Logo Colors
Home
About Us
Services
Projects / Portfolio
Contact Us
Nice to have
• Colors matching our Logo
Should not have
• Black because it doesnt match our logo

```html
<!DOCTYPE html>
<html lang="en">
<head>
<meta charset="utf-8">
<title>Summit Builders</title>
<link href="https://fonts.googleapis.com/css2?family=Roboto:wght@400;500;700;900&display=swap" rel="stylesheet">
<style>
:root{
  --orange:#f15a22;
  --orange-deep:#c9470f;
  --rust:#6a2c10;
  --rust-2:#7d3514;
  --rust-line:#8e3d17;
  --heading:#5a2610;
  --text:#4a3a33;
  --muted:#6e605a;
  --white:#ffffff;
  --cream:#fbe9df;
}
*{margin:0;padding:0;box-sizing:border-box}
html,body{width:1200px;height:4415px;overflow:hidden}
body{position:relative;font-family:'Roboto',sans-serif;color:var(--text);background:var(--white)}
.abs{position:absolute}
.topbar{left:0;top:0;width:1200px;height:30px;background:var(--rust);color:var(--white);font-size:13px}
.topbar .social{left:113px;top:10px;display:flex;gap:22px}
.dot{width:10px;height:10px;border-radius:50%;background:var(--white);display:block}
.topbar .phone{left:245px;top:8px}
.topbar .mail{right:112px;top:8px}
.nav{left:0;top:30px;width:1200px;height:70px;background:var(--white);font-size:15px;font-weight:500;color:var(--heading)}
.nav a{position:absolute;top:28px;text-decoration:none;color:inherit}
.nav a.active{color:var(--orange)}
.nav .sep{position:absolute;top:0;width:1px;height:70px;background:#eadcd4}
.quote-btn{position:absolute;left:931px;top:0;width:156px;height:70px;background:var(--orange);color:var(--white);font-size:12px;font-weight:700;display:flex;align-items:center;justify-content:center;gap:6px}
.logo-badge{left:500px;top:-50px;width:200px;height:200px;border-radius:50%;background:var(--white);z-index:3;display:flex;flex-direction:column;align-items:center;justify-content:flex-end;padding-bottom:42px}
.brand-name{font-weight:700;font-size:26px;color:var(--heading);letter-spacing:1px;line-height:1}
.brand-sub{font-weight:500;font-size:10px;color:var(--heading);letter-spacing:4px;margin-top:4px}
.hero{left:0;top:100px;width:1200px;height:680px;background:linear-gradient(135deg,#d8ccbc 0%,#a88f74 40%,#6b5447 70%,#c4b6a4 100%)}
.hero-panel{left:281px;top:285px;width:638px;height:260px;background:rgba(90,40,16,.72);text-align:center;color:var(--white)}
.hero-panel h1{font-size:44px;font-weight:700;margin-top:28px;letter-spacing:.5px}
.hero-panel p{font-size:16px;line-height:28px;margin:12px auto 0;width:560px}
.btn{display:inline-flex;align-items:center;justify-content:center;background:var(--orange);color:var(--white);font-weight:700;border-radius:26px;text-transform:uppercase}
.hero-panel .btn{margin-top:22px;width:186px;height:48px;font-size:15px}
.section-title{width:1200px;text-align:center;font-weight:700;font-size:37px;color:var(--heading);left:0}
.underline{left:565px;width:70px;height:3px;background:var(--orange)}
.who-text{left:210px;top:890px;width:780px;text-align:center;font-size:15px;line-height:29px;color:var(--muted)}
.feature{display:flex;align-items:center;gap:12px;font-size:15px;font-weight:500;line-height:23px;color:var(--heading)}
.why-col{width:230px;text-align:center;color:var(--white)}
.why-col h3{font-size:16px;font-weight:700;margin-top:22px;letter-spacing:.3px}
.why-col p{font-size:15px;line-height:22px;margin-top:10px;color:var(--cream)}
.card{width:310px;height:188px;border:1px solid #e6d8d0;border-top:3px solid var(--orange);border-radius:10px;text-align:center;background:var(--white)}
.card p{font-size:14px;line-height:26px;color:var(--muted);padding:54px 28px 0}
.avatar{width:90px;height:90px;border-radius:50%;background:linear-gradient(160deg,#d9c9bf,#8a6c5c);border:3px solid var(--white);box-shadow:0 0 0 1px #e6d8d0}
.person{width:310px;text-align:center;font-size:15px;font-weight:500;color:var(--heading)}
.person small{font-size:10px;color:var(--muted);font-weight:400}
.stars{color:#f2b200;font-size:13px;letter-spacing:1px;margin-top:4px}
.foot-h{font-size:16px;font-weight:700;color:var(--white)}
.foot-t{font-size:13px;color:var(--cream);line-height:18px}
.foot-label{font-size:11px;font-weight:700;color:var(--white)}
.foot-links{font-size:14px;color:var(--cream);line-height:26px}
</style>
</head>
<body>

<div class="abs topbar">
  <div class="abs social"><span class="dot"></span><span class="dot"></span><span class="dot"></span></div>
  <div class="abs phone">&#9742; +1 555 014 2876</div>
  <div class="abs mail">&#9993; info@summitbuildersca.example</div>
</div>

<div class="abs nav">
  <a class="active" style="left:112px">Home</a>
  <span class="sep" style="left:185px"></span>
  <a style="left:210px">About us</a>
  <span class="sep" style="left:302px"></span>
  <a style="left:330px">Services</a>
  <a style="left:737px">Projects</a>
  <span class="sep" style="left:820px"></span>
  <a style="left:841px">Contact us</a>
  <div class="quote-btn">&#9998; GET A QUOTE</div>
</div>
<div class="abs logo-badge">
  <div class="brand-name">SUMMIT</div>
  <div class="brand-sub">BUILDERS</div>
</div>

<div class="abs hero" role="img" aria-label="Photo of a bright modern kitchen with white cabinets and island"></div>
<div class="abs hero-panel">
  <h1>SUMMIT BUILDERS</h1>
  <p>Lorem ipsum dolor sit amet, consectetur adipiscing elit, sed do eiusmod tempor incididunt ut labore et dolore magna aliqua.</p>
  <span class="btn">Get Started</span>
</div>
<svg class="abs" style="left:0;top:670px" width="1200" height="112" viewBox="0 0 1200 112">
  <polygon points="0,112 600,5 1200,112" fill="#ffffff"/>
  <polyline points="0,110 600,5 1200,110" fill="none" stroke="#f15a22" stroke-width="7"/>
</svg>

<div class="abs section-title" style="top:820px">WHO WE ARE</div>
<p class="abs who-text">We are rethoric question ran over her cheek When she reached the first hills of the Italic Mountains, she had a last view back on the skyline of her hometown Bookmarksgrove, the headline of Alphabet Village and the subline of her own road, the Line Lane.</p>
<div class="abs" style="left:133px;top:1008px;width:960px;height:90px">
  <div class="abs feature" style="left:0;top:0"><svg width="76" height="84" viewBox="0 0 76 84"><polygon points="38,2 74,22 74,62 38,82 2,62 2,22" fill="#f15a22"/><circle cx="38" cy="42" r="15" fill="none" stroke="#fff" stroke-width="3"/><path d="M31 42l5 5 9-10" fill="none" stroke="#fff" stroke-width="3"/></svg><span>We've Repution For<br>Excellence</span></div>
  <div class="abs feature" style="left:264px;top:0"><svg width="76" height="84" viewBox="0 0 76 84"><polygon points="38,2 74,22 74,62 38,82 2,62 2,22" fill="#f15a22"/><path d="M22 44l10-10 6 6 6-6 10 10-16 14z" fill="none" stroke="#fff" stroke-width="3"/></svg><span>We Build<br>Partnerships</span></div>
  <div class="abs feature" style="left:506px;top:0"><svg width="76" height="84" viewBox="0 0 76 84"><polygon points="38,2 74,22 74,62 38,82 2,62 2,22" fill="#f15a22"/><circle cx="38" cy="32" r="9" fill="none" stroke="#fff" stroke-width="3"/><rect x="24" y="46" width="28" height="14" fill="none" stroke="#fff" stroke-width="3"/></svg><span>Guided By<br>Commitment</span></div>
  <div class="abs feature" style="left:748px;top:0"><svg width="76" height="84" viewBox="0 0 76 84"><polygon points="38,2 74,22 74,62 38,82 2,62 2,22" fill="#f15a22"/><circle cx="38" cy="34" r="8" fill="#fff"/><path d="M24 60c0-10 6-16 14-16s14 6 14 16" fill="none" stroke="#fff" stroke-width="3"/></svg><span>A Team Of<br>Professionals</span></div>
</div>

<svg class="abs" style="left:0;top:1190px" width="1200" height="750" viewBox="0 0 1200 750" role="img" aria-label="Services wheel over an orange-toned construction site photo">
  <defs>
    <linearGradient id="svcBg" x1="0" y1="0" x2="1" y2="1">
      <stop offset="0" stop-color="#c9460f"/><stop offset=".5" stop-color="#ee6a1e"/><stop offset="1" stop-color="#b83c0b"/>
    </linearGradient>
    <g id="house"><path d="M-14 10v-12l14-11 14 11v12z" fill="#7d3514"/></g>
  </defs>
  <polygon points="0,90 600,10 1200,115 1200,645 600,738 0,636" fill="url(#svcBg)"/>
  <polyline points="0,92 600,12 1200,117" fill="none" stroke="#6a2c10" stroke-width="10"/>
  <polyline points="0,634 600,736 1200,643" fill="none" stroke="#6a2c10" stroke-width="10"/>
  <text x="600" y="160" text-anchor="middle" font-family="Roboto, sans-serif" font-size="38" font-weight="700" fill="#fff">OUR SERVICES</text>
  <line x1="510" y1="202" x2="575" y2="202" stroke="#fff" stroke-width="1.5"/>
  <line x1="625" y1="202" x2="690" y2="202" stroke="#fff" stroke-width="1.5"/>
  <circle cx="586" cy="202" r="4" fill="#6a2c10"/><circle cx="600" cy="202" r="6" fill="#6a2c10"/><circle cx="614" cy="202" r="4" fill="#6a2c10"/>
  <path d="M311 695 A290 290 0 1 1 871 695" fill="none" stroke="#e3d6cf" stroke-width="14" stroke-linecap="round"/>
  <g font-family="Roboto, sans-serif" font-size="17" font-weight="700" fill="#fff">
    <text x="218" y="280">MOLD</text>
    <polyline points="210,288 375,288 420,340" fill="none" stroke="#6a2c10" stroke-width="2.5"/>
    <text x="122" y="381">WATER DAMAGE</text>
    <polyline points="115,390 300,390 325,425" fill="none" stroke="#6a2c10" stroke-width="2.5"/>
    <text x="106" y="490">FIRE DAMAGE</text>
    <polyline points="100,499 250,499 275,540" fill="none" stroke="#6a2c10" stroke-width="2.5"/>
    <text x="592" y="255" text-anchor="middle">ADUS</text>
    <polyline points="512,264 668,264" fill="none" stroke="#6a2c10" stroke-width="2.5"/>
    <line x1="591" y1="264" x2="591" y2="292" stroke="#6a2c10" stroke-width="2.5"/>
    <text x="852" y="283">RESTORATION</text>
    <polyline points="975,292 815,292 762,340" fill="none" stroke="#6a2c10" stroke-width="2.5"/>
    <text x="993" y="388">REMODEL</text>
    <polyline points="1075,397 915,397 858,425" fill="none" stroke="#6a2c10" stroke-width="2.5"/>
    <text x="924" y="520">LIGHT COMMERCIAL</text>
    <polyline points="1100,529 925,529 905,545" fill="none" stroke="#6a2c10" stroke-width="2.5"/>
  </g>
  <g fill="#fff" stroke="#7d3514" stroke-width="5">
    <circle cx="591" cy="330" r="38"/><circle cx="446" cy="369" r="38"/><circle cx="353" cy="454" r="38"/><circle cx="305" cy="570" r="38"/>
    <circle cx="736" cy="369" r="38"/><circle cx="829" cy="454" r="38"/><circle cx="877" cy="570" r="38"/>
  </g>
  <rect x="575" y="315" width="32" height="30" fill="#7d3514"/>
  <use href="#house" x="446" y="371"/><use href="#house" x="353" y="456"/><use href="#house" x="305" y="572"/>
  <use href="#house" x="736" y="371"/><use href="#house" x="829" y="456"/>
  <rect x="863" y="559" width="28" height="22" rx="3" fill="#7d3514"/>
  <text x="591" y="560" text-anchor="middle" font-family="Roboto, sans-serif" font-size="30" font-weight="700" fill="#fff">SUMMIT</text>
  <text x="591" y="594" text-anchor="middle" font-family="Roboto, sans-serif" font-size="30" font-weight="700" fill="#fff">BUILDERS</text>
</svg>

<div class="abs section-title" style="top:1974px">PROJECT GALLERY</div>
<div class="abs underline" style="top:2025px;left:555px;width:90px"></div>
<div class="abs" style="left:113px;top:2067px;width:485px;height:281px;background:linear-gradient(160deg,#d9cdb5,#a89a82 55%,#4a6a7f)" role="img" aria-label="Photo of a high school building facade"></div>
<div class="abs" style="left:602px;top:2067px;width:485px;height:281px;background:linear-gradient(180deg,#6b6f9a,#c0a9b4 45%,#5a5048)" role="img" aria-label="Photo of a two-storey house at dusk"></div>
<div class="abs" style="left:113px;top:2353px;width:326px;height:302px;background:linear-gradient(180deg,#3f78c9,#9a6f5e 55%,#3f6a2e)" role="img" aria-label="Photo of a brick family home with garages"></div>
<div class="abs" style="left:444px;top:2353px;width:314px;height:302px;background:linear-gradient(180deg,#3a8ed8,#d8c04a 50%,#2f8d3a 75%,#2d6fa8)" role="img" aria-label="Photo of a yellow mansion beside a stream"></div>
<div class="abs" style="left:763px;top:2353px;width:324px;height:302px;background:linear-gradient(180deg,#5f93d4,#8b8d87 50%,#3d6a30)" role="img" aria-label="Photo of a grey craftsman style home"></div>
<div class="abs btn" style="left:492px;top:2701px;width:216px;height:48px;font-size:14px">See All Projects &#10140;</div>

<svg class="abs" style="left:0;top:2855px" width="1200" height="580" viewBox="0 0 1200 580">
  <polygon points="0,90 600,4 1200,90 1200,575 600,530 0,575" fill="#6a2c10"/>
  <polyline points="0,90 600,4 1200,90" fill="none" stroke="#f15a22" stroke-width="8"/>
</svg>
<div class="abs section-title" style="top:2967px;color:#fff">WHY CHOOSE US</div>
<div class="abs underline" style="top:3018px;left:540px;width:120px"></div>
<div class="abs why-col" style="left:104px;top:3100px"><svg width="44" height="46" viewBox="0 0 44 46"><rect x="8" y="4" width="26" height="34" fill="none" stroke="#fff" stroke-width="2"/><line x1="13" y1="14" x2="29" y2="14" stroke="#fff" stroke-width="2"/><line x1="13" y1="21" x2="29" y2="21" stroke="#fff" stroke-width="2"/><circle cx="32" cy="34" r="6" fill="none" stroke="#fff" stroke-width="2"/></svg><h3>CERTIFIED PERSONNEL</h3><p>Lorem ipsum dolor sit amet, consectetur adipiscing elit, sed eiusmod tempor incididunt</p></div>
<div class="abs why-col" style="left:358px;top:3100px"><svg width="44" height="46" viewBox="0 0 44 46"><path d="M6 30l10 8h18l6-8" fill="none" stroke="#fff" stroke-width="2"/><circle cx="23" cy="16" r="9" fill="none" stroke="#fff" stroke-width="2"/><path d="M19 16l3 3 5-6" fill="none" stroke="#fff" stroke-width="2"/></svg><h3>HIGH QUALITY WORK</h3><p>Lorem ipsum dolor sit amet, consectetur adipiscing elit, sed eiusmod tempor incididunt</p></div>
<div class="abs why-col" style="left:612px;top:3100px"><svg width="44" height="46" viewBox="0 0 44 46"><circle cx="22" cy="12" r="7" fill="none" stroke="#fff" stroke-width="2"/><path d="M10 40c0-10 5-16 12-16s12 6 12 16" fill="none" stroke="#fff" stroke-width="2"/></svg><h3>PROFESSIONAL TEAM</h3><p>Lorem ipsum dolor sit amet, consectetur adipiscing elit, sed eiusmod tempor incididunt</p></div>
<div class="abs why-col" style="left:865px;top:3100px"><svg width="44" height="46" viewBox="0 0 44 46"><rect x="8" y="6" width="24" height="34" fill="none" stroke="#fff" stroke-width="2"/><line x1="13" y1="16" x2="27" y2="16" stroke="#fff" stroke-width="2"/><line x1="13" y1="23" x2="27" y2="23" stroke="#fff" stroke-width="2"/><circle cx="34" cy="12" r="6" fill="none" stroke="#fff" stroke-width="2"/></svg><h3>YEARS OF EXPERIENCE</h3><p>Lorem ipsum dolor sit amet, consectetur adipiscing elit, sed eiusmod tempor incididunt</p></div>

<div class="abs section-title" style="top:3487px;font-size:34px">WHAT OUR CLIENTS SAY?</div>
<div class="abs card" style="left:110px;top:3605px"><p>and for all the wonderful work you and your crew are doing. Our team has nothing but good things to say - we are really fortunate to have found you for</p></div>
<div class="abs card" style="left:444px;top:3605px"><p>Summit Builders is one of the best general contractors we've worked with. The entire team tactfully delivered a project of exceptional quality while</p></div>
<div class="abs card" style="left:778px;top:3605px"><p>Lorem ipsum dolor sit consectetur adipiscing elit, sed do eiusmod tempor incididunt ut labore et dolore magna aliqua. Ut enim ad minim veniam,</p></div>
<div class="abs avatar" style="left:220px;top:3558px" role="img" aria-label="Client portrait"></div>
<div class="abs avatar" style="left:554px;top:3558px" role="img" aria-label="Client portrait"></div>
<div class="abs avatar" style="left:888px;top:3558px" role="img" aria-label="Client portrait"></div>
<div class="abs person" style="left:110px;top:3816px">Dana Whitfield, <small>Chairman KLT</small><div class="stars">&#9733;&#9733;&#9733;&#9733;&#9733;</div></div>
<div class="abs person" style="left:444px;top:3816px">Lena Ortiz, <small>Project Manager</small><div class="stars">&#9733;&#9733;&#9733;&#9733;&#9733;</div></div>
<div class="abs person" style="left:778px;top:3816px">Sam Porter, <small>Chairman KLT</small><div class="stars">&#9733;&#9733;&#9733;&#9733;&#9733;</div></div>

<svg class="abs" style="left:0;top:3945px" width="1200" height="470" viewBox="0 0 1200 470">
  <polygon points="0,92 600,6 1200,92 1200,470 0,470" fill="#6a2c10"/>
  <polyline points="0,92 600,6 1200,92" fill="none" stroke="#f15a22" stroke-width="8"/>
</svg>
<div class="abs" style="left:128px;top:4140px;width:170px;text-align:center">
  <div style="font-size:34px;font-weight:700;color:#fff;letter-spacing:1px">SUMMIT</div>
  <div style="font-size:13px;color:#fff;letter-spacing:6px;margin-top:2px">BUILDERS</div>
  <div style="font-size:11px;color:var(--cream);margin-top:22px">CSLB License # 2418596</div>
  <div style="display:flex;gap:16px;justify-content:center;margin-top:22px"><span class="dot"></span><span class="dot"></span><span class="dot"></span><span class="dot"></span></div>
</div>
<div class="abs foot-h" style="left:369px;top:4100px">Our Office Address</div>
<div class="abs" style="left:369px;top:4140px">
  <div class="foot-label"><span style="color:var(--orange)">&#9742;</span> Phone</div><div class="foot-t" style="margin-left:24px">555-014-2876</div>
  <div class="foot-label" style="margin-top:14px"><span style="color:var(--orange)">&#9993;</span> Email</div><div class="foot-t" style="margin-left:24px">info@summitbuildersca.example</div>
  <div class="foot-label" style="margin-top:14px"><span style="color:var(--orange)">&#9679;</span> Location</div><div class="foot-t" style="margin-left:24px">412 W Orchard Ave Fairview,<br>CA 90000</div>
</div>
<div class="abs foot-h" style="left:672px;top:4100px">Company</div>
<div class="abs foot-links" style="left:672px;top:4138px">Home<br>About us<br>Services<br>Projects<br>Contact us</div>
<div class="abs foot-h" style="left:862px;top:4100px">Stil have questions?</div>
<div class="abs foot-t" style="left:862px;top:4140px;width:240px">Contact us using this form. A representative will aswer your questions as soon as possible.</div>
<div class="abs btn" style="left:862px;top:4225px;width:198px;height:40px;font-size:14px">Get In Touch</div>
<div class="abs btn" style="left:1008px;top:4306px;width:80px;height:22px;font-size:10px;background:#fff;color:var(--heading)">&#9650; Go Up</div>
<div class="abs" style="left:113px;top:4352px;width:974px;height:1px;background:var(--rust-line)"></div>
<div class="abs foot-t" style="left:113px;top:4366px">© 2020 Summit Builders | All Rights Reserved</div>
<div class="abs foot-t" style="right:113px;top:4366px">Privacy Policy &nbsp;|&nbsp; Cookie Policy &nbsp;|&nbsp; Terms Of Services</div>

</body>
</html>
```